New business card/stationary for a consulting company

I am looking for a clean and very professional looking business card for my consulting company as well as corresponding stationary. I am uploading our logo. I like simple and powerful for the feel. No graphics but I am open on everything else. Below is my contact information but would like the final to be in a version I can add my employees information into and print. Thank you.

Daniel Whitcombe
dan@ferncliffadvisory.com
2870 North 9th Avenue, Summit Floor, Elm Ridge, Illinois 60531
www.ferncliffadvisory.com

Industry/Entity Type

Consulting

Contact Information for Business Card

Daniel Whitcombe
dan@ferncliffadvisory.com
www.ferncliffadvisory.com

Font styles to use
Serif
Sans Serif

Requirements
Must have
• Our logo and the business card details.
Nice to have
• our website www.ferncliffadvisory.com

```html
<!DOCTYPE html>
<html lang="en">
<head>
<meta charset="utf-8">
<title>Ferncliff Advisory – Business Card</title>
<link rel="stylesheet" href="https://fonts.googleapis.com/css2?family=Didact+Gothic&family=PT+Sans:wght@400;700&display=swap">
<style>
  :root {
    --backdrop: #3b3531;
    --card: #151515;
    --card-edge: #222;
    --ink: #f2f2f2;
    --ink-soft: #bdbdbd;
    --ink-muted: #8a8a8a;
    --rule: #cfcfcf;
  }
  * { box-sizing: border-box; margin: 0; padding: 0; }
  html, body { width: 1200px; height: 864px; overflow: hidden; }
  body {
    background: var(--backdrop);
    display: flex;
    align-items: center;
    justify-content: center;
    gap: 56px;
    font-family: "PT Sans", sans-serif;
  }
  .card {
    position: relative;
    width: 540px;
    height: 309px;
    background: var(--card);
    border: 1px solid var(--card-edge);
    box-shadow: 0 14px 30px rgba(0,0,0,.45);
    color: var(--ink);
  }

  /* Front */
  .card--front {
    display: flex;
    flex-direction: column;
    align-items: center;
    justify-content: center;
    gap: 26px;
  }
  .brand {
    display: flex;
    align-items: center;
    gap: 12px;
    font-family: "Didact Gothic", sans-serif;
    font-size: 22px;
    letter-spacing: 0.06em;
    text-transform: uppercase;
    white-space: nowrap;
  }
  .brand__mark {
    width: 14px;
    height: 14px;
    background: currentColor;
  }
  .card--front .brand { color: var(--ink-soft); }
  .front-web {
    font-family: "Didact Gothic", sans-serif;
    font-size: 12px;
    letter-spacing: 0.42em;
    color: var(--ink-muted);
  }

  /* Back */
  .card--back .brand {
    position: absolute;
    top: 52px;
    right: 30px;
    font-size: 17px;
  }
  .holder {
    position: absolute;
    left: 30px;
    top: 112px;
  }
  .holder__name {
    font-weight: 700;
    font-size: 16px;
    letter-spacing: 0.02em;
    text-transform: uppercase;
    margin-bottom: 8px;
  }
  .holder__address {
    font-style: normal;
    font-size: 12px;
    line-height: 1.35;
    color: var(--ink);
  }
  .rule {
    position: absolute;
    left: 30px;
    right: 30px;
    height: 1px;
    background: var(--rule);
  }
  .rule--mid { top: 196px; left: 200px; }
  .rule--low { top: 280px; left: 340px; }
  .contact {
    position: absolute;
    right: 30px;
    top: 220px;
    list-style: none;
    text-align: right;
    font-size: 12.5px;
    line-height: 1.5;
  }
  .contact li { display: flex; align-items: center; justify-content: flex-end; gap: 7px; }
  .contact svg { width: 11px; height: 11px; fill: var(--ink); }
</style>
</head>
<body>

  <section class="card card--front" aria-label="Card front">
    <div class="brand"><span class="brand__mark"></span>Ferncliff Advisory</div>
    <p class="front-web">www.ferncliffadvisory.com</p>
  </section>

  <section class="card card--back" aria-label="Card back">
    <div class="brand"><span class="brand__mark"></span>Ferncliff Advisory</div>

    <div class="holder">
      <h1 class="holder__name">Daniel Whitcombe</h1>
      <address class="holder__address">
        2870 North 9th Avenue<br>
        Summit Floor, Elm Ridge<br>
        Illinois 60531
      </address>
    </div>

    <div class="rule rule--mid"></div>

    <ul class="contact">
      <li>dan@ferncliffadvisory.com
        <svg viewBox="0 0 12 12" aria-hidden="true"><path d="M1 3h10v7H1z"/><path d="M1 3l5 4 5-4" fill="none" stroke="#151515" stroke-width="1"/></svg>
      </li>
      <li>www.ferncliffadvisory.com
        <svg viewBox="0 0 12 12" aria-hidden="true"><circle cx="6" cy="6" r="5"/><circle cx="6" cy="6" r="2" fill="#151515"/></svg>
      </li>
    </ul>

    <div class="rule rule--low"></div>
  </section>

</body>
</html>
```